Copperleaf Roofing Business Card

This is my current business card. But I’d like to make some changes. Somewhere on the card I’d like to list some of the services we offer. Maybe on the back? But I’d still like to keep the red. White and black modern look.

-residential & commercial roofing
-Roof Repairs & Maintenance
-Storm Damage & Insurance Claims specialist
-Christmas Lights and permanent Christmas lights
Fencing. Windows. Gutters. Siding. Sheetrock, painting.

```html
<!DOCTYPE html>
<html lang="en">
<head>
<meta charset="utf-8">
<title>Copperleaf Roofing Co. – Business Card</title>
<link href="https://fonts.googleapis.com/css2?family=Michroma&family=Montserrat:wght@400;500;600&display=swap" rel="stylesheet">
<style>
  :root {
    --backdrop: #2a2a2a;
    --card: #ffffff;
    --ink: #151515;
    --red: #e3202a;
    --muted: #3a3a3a;
  }
  * { box-sizing: border-box; margin: 0; padding: 0; }
  html, body { width: 1200px; height: 875px; overflow: hidden; }
  body {
    background: var(--backdrop);
    font-family: "Montserrat", sans-serif;
    color: var(--ink);
    position: relative;
  }
  .card {
    position: absolute;
    left: 260px;
    width: 680px;
    height: 388px;
    background: var(--card);
    border-radius: 22px;
  }
  .card--front { top: 34px; }
  .card--back { top: 453px; }

  /* Brand lockup */
  .brand {
    display: flex;
    align-items: center;
    gap: 18px;
  }
  .brand__dot {
    border-radius: 50%;
    background: var(--red);
    flex: none;
  }
  .brand__name {
    font-family: "Michroma", sans-serif;
    color: var(--ink);
    text-transform: uppercase;
    line-height: 1.25;
    letter-spacing: 0.02em;
  }
  .card--front .brand {
    position: absolute;
    left: 50%; top: 50%;
    transform: translate(-50%, -50%);
    flex-direction: column;
    gap: 22px;
    text-align: center;
  }
  .card--front .brand__dot { width: 120px; height: 120px; }
  .card--front .brand__name { font-size: 34px; }

  .card--back .brand {
    position: absolute;
    right: 40px; top: 34px;
  }
  .card--back .brand__dot { width: 62px; height: 62px; }
  .card--back .brand__name { font-size: 20px; }

  .rule {
    position: absolute;
    height: 1.5px;
    background: var(--red);
  }
  .rule--top { left: 40px; right: 40px; top: 124px; }

  /* Services */
  .services {
    position: absolute;
    right: 40px; top: 144px;
    list-style: none;
    text-align: right;
    font-size: 13.5px;
    line-height: 1.55;
    color: var(--ink);
  }
  .services li::after {
    content: "";
    display: inline-block;
    width: 6px; height: 6px;
    border-radius: 50%;
    background: var(--red);
    margin-left: 9px;
    vertical-align: middle;
  }

  /* Person */
  .person {
    position: absolute;
    left: 40px; top: 170px;
  }
  .person__name {
    font-family: "Michroma", sans-serif;
    font-size: 25px;
    letter-spacing: 0.03em;
    text-transform: uppercase;
  }
  .person__name .accent { color: var(--red); }
  .person__role {
    font-size: 14px;
    color: var(--muted);
    margin-top: 4px;
  }
  .rule--person { left: 40px; width: 290px; top: 244px; }

  /* Contact */
  .contact {
    position: absolute;
    left: 40px; top: 264px;
    list-style: none;
    font-size: 14.5px;
    line-height: 1;
  }
  .contact li {
    display: flex;
    align-items: center;
    gap: 10px;
    margin-bottom: 11px;
  }
  .contact svg { width: 15px; height: 15px; flex: none; }
</style>
</head>
<body>

  <section class="card card--front" aria-label="Business card front">
    <div class="brand">
      <span class="brand__dot"></span>
      <span class="brand__name">Copperleaf<br>Roofing Co.</span>
    </div>
  </section>

  <section class="card card--back" aria-label="Business card back">
    <div class="brand">
      <span class="brand__dot"></span>
      <span class="brand__name">Copperleaf<br>Roofing Co.</span>
    </div>
    <div class="rule rule--top"></div>

    <ul class="services">
      <li>Residential &amp; commercial roofing</li>
      <li>Roof Repairs &amp; Maintenance</li>
      <li>Storm Damage &amp; Insurance Claims specialist</li>
      <li>Fencing. Windows. Gutters.</li>
      <li>Siding. Sheetrock, painting</li>
    </ul>

    <div class="person">
      <p class="person__name">Dale <span class="accent">Mercer</span></p>
      <p class="person__role">Owner</p>
    </div>
    <div class="rule rule--person"></div>

    <ul class="contact">
      <li>
        <svg viewBox="0 0 16 16" aria-hidden="true"><path fill="#e3202a" d="M3.6 1.5l2.2 2.6-1.3 1.7c.8 1.8 2.2 3.2 4 4l1.7-1.3 2.6 2.2-1.2 2.3C7 12.8 3.2 9 1.3 2.7z"/></svg>
        <span>682-555-0147</span>
      </li>
      <li>
        <svg viewBox="0 0 16 16" aria-hidden="true"><rect x="1" y="3.5" width="14" height="9.5" rx="1.2" fill="#e3202a"/><path d="M1.5 4.2L8 9l6.5-4.8" fill="none" stroke="#fff" stroke-width="1.2"/></svg>
        <span>dale@copperleafroofing.com</span>
      </li>
      <li>
        <svg viewBox="0 0 16 16" aria-hidden="true"><circle cx="8" cy="8" r="6.5" fill="none" stroke="#e3202a" stroke-width="1.5"/><ellipse cx="8" cy="8" rx="2.8" ry="6.5" fill="none" stroke="#e3202a" stroke-width="1.2"/><path d="M1.5 8h13" stroke="#e3202a" stroke-width="1.2"/></svg>
        <span>www.copperleafroofing.com</span>
      </li>
    </ul>
  </section>

</body>
</html>
```